Contemporary Business card for Event Manager

Needed for my startup events company in Melbourne. Events I manage will be based within the fashion industry, sporting events, product launches etc. Not weddings or small dinner parties. Therfore I am after something professional and aimed at high end corporate market; but with the added emphasis on not being too conservative or boring. I am happy with a pop of colour e.g. yellow or copper foil.

Target Market(s)

fashion industry, design industry, high end sporting events e.g. Polo, Grand Prix, corporate clients,

Industry/Entity Type

Fashion

Contact Information for Business Card

side 1
Lucy Brandt (can be upper or lower case, have a feature full stop between first and surname, or at the end of the nameetc) I am open to ideas. I would also be fine with my initials or name as a logo on the front (if this is the case my full name would need to go on the second side of the card.
2nd side:
Mobile: +61 400 817 263
email: lucy.brandt@mailnest.com.au

on one side of the card:
event management | brand activation | Advisory Services

Font styles to use
Serif
Sans Serif

Requirements
Must have
• side 2 must have
• mobile number
• email address
• event management | brand activation | Advisory Services
• ** my full name (Lucy Brandt) must be on the card somewhere)
Nice to have
• 1st side
• I see the card stock being either a dark grey, light grey, natural white or black (all matt colours on unprocessed card). I see the writing being copper foil, or foil white or foil black.
• To give you a feel for me, think: contemporary, minimalist, I love line drawings, concrete, white with grey vein marble, copper, white, grey, black...yes I do like colour....yellow (but pops of colour) ;) I would like the card to look designer but 'on trend' as I deal with a lot of design and fashion clients....styles - think the sophistication and simplicity of Vireaux or urban contemporary.
• some examples of what I like. Although please don't leet this limit you...I really am happy to have something a little more urban or design focused like a line drawing of an object, person too or a photo image too.
• https://www.moodtackle.com/pin/830165427719302846/
• https://www.moodtackle.com/pin/607281935540173268/
• https://www.moodtackle.com/pin/318746205913457092/
• https://www.moodtackle.com/pin/41983627530918476/
• https://www.moodtackle.com/pin/53128940672419087/
• https://www.moodtackle.com/pin/90316284750638152/
• https://www.moodtackle.com/pin/734092618450362918/
• https://www.moodtackle.com/pin/926354081736215407/
• https://www.moodtackle.com/pin/481627093518704356/
Should not have
• should not look commercial or have cartoonish looking logos. However happy with a simple line drawing or logo with initials etc.

```html
<!DOCTYPE html>
<html lang="en">
<head>
<meta charset="utf-8">
<title>Lucy Brandt — Business Card</title>
<link rel="stylesheet" href="https://fonts.googleapis.com/css2?family=Tinos:ital,wght@0,400;1,400&display=swap">
<style>
  :root {
    --backdrop: #e6e4e6;
    --card-black: #111111;
    --accent-yellow: #f7e212;
    --edge-white: #ffffff;
    --ink-black: #0b0b0b;
    --ink-white: #ffffff;
  }
  * { margin: 0; padding: 0; box-sizing: border-box; }
  html, body {
    width: 1200px;
    height: 862px;
    overflow: hidden;
    background: var(--backdrop);
  }
  .canvas {
    position: relative;
    width: 1200px;
    height: 862px;
    font-family: "Tinos", "Times New Roman", serif;
  }
  .card {
    position: absolute;
    top: 161px;
    width: 330px;
    height: 540px;
    background: var(--card-black);
    box-shadow: 0 18px 40px rgba(0,0,0,0.25);
    overflow: hidden;
  }
  .card--front { left: 230px; }
  .card--back { left: 640px; }
  .card__shapes {
    position: absolute;
    inset: 0;
    width: 100%;
    height: 100%;
    display: block;
  }
  .card__name {
    position: absolute;
    top: 210px;
    width: 100%;
    text-align: center;
    color: var(--ink-white);
    font-size: 27px;
    letter-spacing: 0.5px;
    text-transform: uppercase;
  }
  .card__front-email {
    position: absolute;
    top: 488px;
    width: 100%;
    text-align: center;
    color: var(--ink-black);
    font-size: 15px;
  }
  .card__dash {
    position: absolute;
    top: 517px;
    left: 148px;
    width: 34px;
    height: 3px;
    background: var(--ink-black);
  }
  .card__phone {
    position: absolute;
    top: 132px;
    width: 100%;
    text-align: center;
    color: var(--ink-black);
    font-size: 37px;
    letter-spacing: 0.5px;
  }
  .card__email {
    position: absolute;
    top: 392px;
    width: 100%;
    text-align: center;
    color: var(--accent-yellow);
    font-size: 16px;
  }
  .card__services {
    position: absolute;
    top: 444px;
    width: 100%;
    list-style: none;
    text-align: center;
    color: var(--accent-yellow);
    font-size: 17px;
    line-height: 22px;
  }
</style>
</head>
<body>
<main class="canvas">

  <section class="card card--front" aria-label="Card front">
    <svg class="card__shapes" viewBox="0 0 330 540" aria-hidden="true">
      <polygon points="0,465 200,439 330,486 330,540 0,540" fill="var(--edge-white)"/>
      <polygon points="0,470 200,446 330,491 330,540 0,540" fill="var(--accent-yellow)"/>
    </svg>
    <h1 class="card__name">Lucy Brandt.</h1>
    <p class="card__front-email">lucy.brandt@mailnest.com.au</p>
    <span class="card__dash" aria-hidden="true"></span>
  </section>

  <section class="card card--back" aria-label="Card back">
    <svg class="card__shapes" viewBox="0 0 330 540" aria-hidden="true">
      <polygon points="0,58 160,116 330,66 330,264 185,204 0,242" fill="var(--edge-white)"/>
      <polygon points="0,60 160,120 330,69 330,265 185,210 0,240" fill="var(--accent-yellow)"/>
      <polygon points="148,296 182,296 164,308" fill="var(--accent-yellow)"/>
    </svg>
    <p class="card__phone">61 400 817 263</p>
    <p class="card__email">lucy.brandt@mailnest.com.au</p>
    <ul class="card__services">
      <li>event management</li>
      <li>brand activation</li>
      <li>Advisory Services</li>
    </ul>
  </section>

</main>
</body>
</html>
```